9x12 Business Brochure, 3 fold, for Internet Marketing Company

I'd like to have a brochure designed for my Internet marketing company. I have the content all ready, 10 Internet Marketing Myths, which you can see here: http://www.brisklanternstudio.example/usual-web-promotion-fables/. I'm looking for something creative and business to business. The company is all about Internet marketing. I like the "http://" header I use at our website. People like it too and identify with it. Audience is business owners 35 to 55 years old. I use blue at my website. I *think* I would like the cover page (front page) to open with some attention grabbing text, that basically takes most of the front page of the brochure. It would probably say: "I Can Help You Get BETTER RESULTS from Your Website, More Traffic, TOP RANKINGS at Quorble, More Leads and MORE SALES. But first you'll have to avoid these common Internet marketing myths..." The inside pages would have the content from above (the 10 myths). The back page would have testimonials that I can provide. And the inside folded in page (or what I call the inside folded in page) would have a list of services. I think I want the dimensions 12x9 which is a larger sized, three-fold brochure.

Target Market(s)

I use this brochure to send to business owners and managers to show them I know what I'm talking about and and expert. See attachment for content.

Industry/Entity Type

Marketing

Requirements
Should not have
• No clipart. Probably not illustrations. Photos. The "http://" used at the site is something people "connect" with and get that this is about Internet marketing.

```html
<!DOCTYPE html>
<html lang="en">
<head>
<meta charset="utf-8">
<title>Common Internet Marketing Myths – Brochure Inside Spread</title>
<link rel="stylesheet" href="https://fonts.googleapis.com/css2?family=Open+Sans:wght@400;600;700&family=Roboto+Condensed:ital,wght@0,400;0,700;1,400&display=swap">
<style>
  :root {
    --stage: #e6e6e6;
    --panel-blue: #4a86b9;
    --panel-blue-light: #5e97c6;
    --panel-blue-dark: #3f78a8;
    --band-dark: #333536;
    --band-mid: #4a4c4e;
    --accent-blue: #3f7db5;
    --text-dark: #3a3a3a;
    --text-light: #ffffff;
    --rule-light: rgba(255,255,255,0.55);
    --rule-dark: #9aa7b3;
  }
  * { margin: 0; padding: 0; box-sizing: border-box; }
  html, body { width: 1200px; height: 924px; overflow: hidden; }
  body { background: var(--stage); font-family: "Open Sans", Arial, sans-serif; }

  .brochure {
    position: absolute; left: 20px; top: 15px;
    width: 1160px; height: 894px;
    box-shadow: 0 2px 10px rgba(0,0,0,0.25);
  }
  .panel { position: absolute; top: 0; height: 894px; width: 387px; }
  .panel--left { left: 0; background: linear-gradient(160deg, var(--panel-blue-light), var(--panel-blue) 45%, var(--panel-blue-dark)); }
  .panel--middle { left: 387px; width: 386px; background: linear-gradient(180deg, #d4d6d8 0%, #ffffff 12%, #ffffff 55%, #e4eef6 80%, #cfe0ee 100%); }
  .panel--right { left: 773px; background: linear-gradient(200deg, var(--panel-blue-light), var(--panel-blue) 45%, var(--panel-blue-dark)); }

  .header-band {
    position: absolute; left: 0; top: 30px; width: 1160px; height: 67px;
    background: linear-gradient(180deg, var(--band-mid), var(--band-dark));
  }
  .header-band svg { position: absolute; left: 0; top: 0; }
  .header-title {
    position: absolute; left: 45px; top: 13px;
    font-family: "Roboto Condensed", Arial, sans-serif; font-weight: 700;
    font-size: 29px; color: var(--text-light); letter-spacing: 0.5px;
  }
  .header-call {
    position: absolute; right: 32px; top: 18px;
    font-family: "Roboto Condensed", Arial, sans-serif; color: var(--text-light);
    font-size: 18px; font-style: italic;
  }
  .header-call strong { font-style: normal; font-weight: 700; font-size: 23px; }

  .myth { position: absolute; left: 29px; width: 330px; }
  .myth-label {
    display: flex; align-items: center; gap: 6px;
    font-size: 14px; color: var(--text-light); opacity: 0.9;
  }
  .myth-label::after { content: ""; flex: 1; height: 1px; background: var(--rule-light); }
  .myth-title {
    font-size: 16.5px; font-weight: 600; color: var(--text-light);
    line-height: 1.2; margin: 2px 0 10px;
  }
  .myth-body { font-size: 10.9px; line-height: 17px; color: var(--text-light); text-align: justify; }

  .panel--middle .myth-label { color: var(--text-dark); }
  .panel--middle .myth-label::after { background: var(--rule-dark); }
  .panel--middle .myth-title { color: var(--accent-blue); }
  .panel--middle .myth-body { color: var(--text-dark); }

  .slogan-band {
    position: absolute; left: 0; top: 761px; width: 386px; height: 34px;
    background: var(--band-dark); color: var(--text-light);
    font-family: "Roboto Condensed", Arial, sans-serif; font-size: 19px;
    text-align: center; line-height: 34px;
  }
  .contact { position: absolute; left: 0; top: 808px; width: 386px; text-align: center; }
  .contact-name { font-family: "Roboto Condensed", Arial, sans-serif; font-size: 19px; color: var(--accent-blue); }
  .contact-email { font-size: 11px; font-weight: 700; color: #222; margin-top: 2px; }
  .contact-phone { font-family: "Roboto Condensed", Arial, sans-serif; font-weight: 700; font-size: 20px; color: #222; margin-top: 1px; }
</style>
</head>
<body>
<main class="brochure">
  <section class="panel panel--left">
    <article class="myth" style="top:126px">
      <p class="myth-label">Myth #1</p>
      <h2 class="myth-title">If You Build It They Will Come</h2>
      <p class="myth-body">Building a website is no guarantee of online success. If you build it, don’t assume people will find it. This is a guaranteed losing strategy. For your Internet marketing to succeed your website will need quality traffic (i.e. visitor sessions) and then convert those visitors into phone calls and online inquiries.</p>
    </article>
    <article class="myth" style="top:301px">
      <p class="myth-label">Myth #2</p>
      <h2 class="myth-title">Search Engines Are All You’ll Need</h2>
      <p class="myth-body">It is a very common misconception, and costly mistake, to think that search engines and organic search engine positioning is all you need for online success. While a top ranked website is a very valuable asset, and it can drive a lot of qualified traffic to your website, it can take months, or years, to achieve that positioning — if you can get it at all. You’ll need a multi-pronged approach to building traffic, including buying advertising, pay-per-click advertising (PPC), integration of your offline marketing with your online marketing, blogging, social media, and of course, search engine optimization (SEO).</p>
    </article>
    <article class="myth" style="top:556px">
      <p class="myth-label">Myth #3</p>
      <h2 class="myth-title">All Traffic Is Good</h2>
      <p class="myth-body">Not true! To get real results from your website, inquiries, phone calls, and sales, you’ll need to find and attract QUALIFIED traffic – people who are actually getting married and who are ready to purchase your products and services.</p>
    </article>
    <article class="myth" style="top:713px">
      <p class="myth-label">Myth #4</p>
      <h2 class="myth-title">Hits Are A Good Measure Of Success</h2>
      <p class="myth-body">Wrong! If you are measuring “hits” you’re not even in the game. A “hit” is a technical term that describes activity on a hosting server. Unfortunately, most webmasters use this term casually and it is interpreted to mean you have lots of traffic. Hits are not real people. Real people who visit your website are logged as “visitor sessions.”</p>
    </article>
  </section>

  <section class="panel panel--middle">
    <article class="myth" style="top:126px">
      <p class="myth-label">Myth #5</p>
      <h2 class="myth-title">You Can Do This All Yourself</h2>
      <p class="myth-body">If you are in any competitive category of products or services, or in a geographically competitive marketplace, the chances that you can build a website, develop the traffic, and manage your ongoing online marketing ALL BY YOURSELF are less than one in ten. Put another way, DIY has a 90% chance of FAILURE.</p>
    </article>
    <article class="myth" style="top:302px">
      <p class="myth-label">Myth #6</p>
      <h2 class="myth-title">It’s Easy To Get Traffic From Search Engines</h2>
      <p class="myth-body">In today’s competitive marketplace it is more difficult than ever to get top ranking with Quorble, Vexia!, or Zumo. It is very likely going to take six to twelve months to see your website achieve a top ranked position for any competitive keyword/keyword phrase that people are searching for – and that’s only if you have SEO expertise. If your website is new it will take longer.</p>
    </article>
    <article class="myth" style="top:520px">
      <p class="myth-label">Myth #7</p>
      <h2 class="myth-title">Submitting Your Website To Search Engines Actually Works</h2>
      <p class="myth-body">Not true! Submitting your website to the search engines each month is USELESS. Companies or individuals that provide this service will gladly take your money and it is unlikely you’ll see any benefit. The best way to get your website indexed in the search engines is for them to find your website link at another regularly crawled, thematically-similar website. A Quorble Sitemap will also help you get your website indexed and crawled more effectively.</p>
    </article>
    <div class="slogan-band">More Traffic. More Leads. More Sales.</div>
    <div class="contact">
      <p class="contact-name">Dana Whitlow</p>
      <p class="contact-email">dana@whitlowwebadvising.example</p>
      <p class="contact-phone">(866) 555-0148</p>
    </div>
  </section>

  <section class="panel panel--right">
    <article class="myth" style="top:126px">
      <p class="myth-label">Myth #8</p>
      <h2 class="myth-title">Search Engine Optimization Is Easy</h2>
      <p class="myth-body">Search engine optimization is not difficult but there is a lot to it. There are dozens of different variables that must be perfectly managed. Each of these falls into one of two categories: “on-page” variables or “off-page” variables. Add to this hundreds of so-called “experts” and their advice (which is incorrect, incomplete, or misleading), and it’s pretty hard to call the search engine optimization process easy. Getting top ranked is even more challenging when a competitor has hired a reputable SEO expert to help them with their website and Internet marketing strategy.</p>
    </article>
    <article class="myth" style="top:391px">
      <p class="myth-label">Myth #9</p>
      <h2 class="myth-title">Meta-Tags Are The Key To A Top Ranked Website</h2>
      <p class="myth-body">Meta-tags are specific lines of programming code that appear behind-the-scenes at your website. Search engines see them but your visitors do not. Search engines use meta-tags as one of the factors in determining page relevancy. Quorble’s algorithm tries to show the most relevant pages for a search on a search engine results page (SERP). Meta-tags are still important, but only one of more than two dozen factors related to the overall search engine optimization of your website.</p>
    </article>
    <article class="myth" style="top:652px">
      <p class="myth-label">Myth #10</p>
      <h2 class="myth-title">Your Webmaster / Programmer Can Help You With Your Internet Marketing</h2>
      <p class="myth-body">Graphics design, programming code, and page layout are very different from Internet marketing. In most cases, (90% of the time) a webmaster / programmer will not be able to give you the appropriate advice or support to effectively promote and market your website online.</p>
    </article>
  </section>

  <header class="header-band">
    <svg width="1160" height="67" viewBox="0 0 1160 67" aria-hidden="true">
      <polygon points="808,0 836,0 882,67 854,67" fill="#8fb4d6"/>
      <polygon points="840,0 852,0 898,67 886,67" fill="#d8dde2" opacity="0.6"/>
      <line x1="0" y1="66" x2="1160" y2="66" stroke="#6d7072" stroke-width="1"/>
    </svg>
    <h1 class="header-title">Common Internet Marketing Myths</h1>
    <p class="header-call">Call me today -<strong>(866) 555-0148</strong></p>
  </header>
</main>
</body>
</html>
```